WordPress Website for BidLinks Agency

We are in need of a complete WordPress design.

We will be seeking new clients and we want them to have a great idea of what our business does when they get to the page along with the products and services we offer. Our current website is www.mossyharbor.com and it really needs an upgrade. Wordpress would be great but our owner knows HTML as well so he can go in and edit things later if need be. Please apply if you can show what a Search Engine Marketing company does and can explain this information to a lay person. Also, the website should be responsive so it fits mobile, tablet, and desktop settings while changing to these different widths.

Also, we are not an SEO company, per se but an SEM / PPC company that operates on Zorvic BidLinks, Plim Promos, Chatterwall Promos, and other PPC platforms.

Themes are fine just as long as the content and the visuals display what a search engine marketing company does. Really looking for clients to know exactly why a search engine marketing company does when the get to the site, why they should use a search engine marketing company, and the best way to contact us to get a quote.

Here are some other search engine marketing sites that I like in terms of the content and the layout to give an idea of what should be included on the site:
http://www.fendowlabs.com/
http://www.k9rworks.com/
http://www.boulderpartners.com/
http://www.vjnpromo.com/
http://www.halvorteam.com/
http://meetthepinecrew.com/

Please include my new phone number of the website: 866-555-0142.

Thank you, 
Walt 

Target Market(s)

We are a search engine marketing company looking for more clients and want to be able to explain what a search engine marketing company does in layman's terms.

Industry/Entity Type

Marketing

Font styles to use
Sans Serif

Requirements
Must have
• About Us Page
Services Page
Home Page
Success Stories Page
Blog
Social Media links / feeds
Visuals of products / services offered
Jobs page
Nice to have
• Responsive design
Client Login / Space on the site for monthly client payments / Link to CoinTap or Rivermoss

```html
<!DOCTYPE html>
<html lang="en">
<head>
<meta charset="utf-8">
<title>Amberbolt Digital Marketing</title>
<link href="https://fonts.googleapis.com/css2?family=PT+Sans:wght@400;700&display=swap" rel="stylesheet">
<style>
:root{
  --red:#e01b22;
  --red-band:#d91c24;
  --ink:#3a3a3a;
  --muted:#777;
  --light:#f3f3f3;
  --line:#e2e2e2;
  --white:#fff;
}
*{margin:0;padding:0;box-sizing:border-box}
html,body{width:758px;height:1200px;overflow:hidden;background:var(--white)}
body{font-family:"PT Sans",sans-serif;color:var(--ink);position:relative}
.abs{position:absolute}

/* header */
.site-header{position:absolute;left:0;top:0;width:758px;height:87px;border-bottom:1px solid var(--line);background:var(--white)}
.brand{left:44px;top:30px;display:flex;align-items:center;gap:6px}
.brand-mark{width:14px;height:14px;border-radius:50%;background:var(--red)}
.brand-name{font-size:21px;font-weight:700;color:var(--red);letter-spacing:-.3px}
.brand-sub{left:64px;top:56px;font-size:9px;font-weight:700;color:var(--ink)}
.social{right:56px;top:18px;display:flex;gap:3px}
.social span{width:18px;height:18px;border-radius:50%;background:var(--red);display:block}
.main-nav{right:47px;top:50px;display:flex;font-size:11.5px}
.main-nav a{color:#555;text-decoration:none;padding:0 11px;border-left:1px solid #ccc;line-height:15px}
.main-nav a:first-child{border-left:none;color:var(--red)}
.main-nav a:last-child{padding-right:0}

/* hero */
.hero{left:0;top:87px;width:758px;height:288px;background:linear-gradient(180deg,#f2f2f2,#fbfbfb 55%,#f0f0f0);border-bottom:1px solid var(--line)}
.hero-kicker{left:43px;top:68px;font-size:21px;color:#444}
.hero-title{left:43px;top:93px;font-size:35px;color:var(--red);letter-spacing:-.3px}
.hero-text{left:44px;top:135px;width:335px;font-size:9.5px;line-height:14.5px;color:#666}
.hero-dots{left:46px;top:176px;display:flex;gap:2px}
.hero-dots span{width:8px;height:8px;border-radius:50%;background:#bbb}
.hero-dots span:first-child{background:var(--red)}
.hero-visual{left:385px;top:80px;width:300px;height:135px;border-radius:10px;background:linear-gradient(160deg,#e8eef4,#7fb8de 50%,#b9c9d8)}

/* welcome */
.welcome{left:0;top:376px;width:758px;text-align:center}
.welcome h1{margin-top:30px;font-size:23.5px;font-weight:400;color:#333;letter-spacing:-.2px}
.welcome h1 strong{color:var(--red)}
.welcome .lead{margin-top:5px;font-size:13px;color:#666}
.welcome p.body{margin:3px auto 0;width:640px;font-size:9.8px;line-height:15.5px;color:#777}

/* products */
.products{left:0;top:522px;width:758px;height:261px;background:var(--red-band);color:var(--white)}
.products h2{position:absolute;left:46px;top:32px;font-size:20px;font-weight:400}
.product{position:absolute;top:68px;width:162px}
.product .thumb{width:161px;height:79px;border:4px solid var(--white)}
.product h3{margin-top:14px;font-size:11.5px;font-weight:700}
.product p{margin-top:1px;font-size:9.3px;line-height:13.5px}

/* services */
.section-title{font-size:21px;font-weight:400;color:#444}
.section-title strong{font-weight:700}
.services-title{left:45px;top:813px}
.service{position:absolute;width:200px;display:flex;gap:8px}
.service .icon{width:35px;height:35px;border-radius:50%;flex:none;margin-top:2px}
.service h4{font-size:13px;font-weight:400;color:#555}
.service p{margin-top:2px;font-size:9.3px;line-height:13.5px;color:#777}

/* blog */
.blog-title{left:494px;top:813px}
.blog-box{left:493px;top:850px;width:221px;height:209px;border:1px solid #ddd;border-radius:4px;background:var(--white)}
.blog-item{margin:0 11px 0 17px;padding:6px 0 5px;border-bottom:1px solid #e3e3e3}
.blog-item h5{font-size:9.8px;font-weight:400;color:var(--red)}
.blog-item p{font-size:8.7px;line-height:12.5px;color:#888}
.blog-item:last-of-type{border-bottom:none}
.blog-more{position:absolute;left:0;bottom:0;width:100%;height:24px;border-top:1px solid #e3e3e3;background:#fafafa;font-size:8.3px;color:#555;text-align:right;padding:6px 15px 0 0}

/* footer */
.site-footer{left:0;top:1110px;width:758px;height:90px;border-top:2px solid #eee;background:linear-gradient(#f5f5f5,#fff 10px)}
.footer-nav{left:49px;top:27px;font-size:9.5px;color:#444}
.footer-nav span{color:#888;padding:0 4px}
.copyright{left:49px;top:48px;font-size:8.8px;color:#888}
.badge-a{left:553px;top:25px;width:48px;height:32px;background:#555;border-radius:2px}
.badge-b{left:614px;top:25px;width:83px;height:32px;background:#1c5f8f;border-radius:3px}
</style>
</head>
<body>

<header class="site-header">
  <div class="abs brand"><span class="brand-mark"></span><span class="brand-name">Amberbolt</span></div>
  <div class="abs brand-sub">Digital Marketing</div>
  <div class="abs social" aria-label="Social links"><span></span><span></span><span></span><span></span></div>
  <nav class="abs main-nav">
    <a href="#">HOME</a><a href="#">ABOUT US</a><a href="#">PRODUCTS</a><a href="#">SUCCESS STORIES</a><a href="#">BLOG</a><a href="#">CONTACT US</a>
  </nav>
</header>

<section class="abs hero">
  <div class="abs hero-kicker">We are Experiend &amp; Expert in</div>
  <div class="abs hero-title">Explosive Advertising..</div>
  <p class="abs hero-text">Etiam nulla massa, pharetra facilisis, volutpat in, imperdiet sit amet sem Aliquam nec erat at purus cursus interdum. Vestibulum ligula augue</p>
  <div class="abs hero-dots"><span></span><span></span><span></span><span></span></div>
  <div class="abs hero-visual" role="img" aria-label="Smartphone with a rising red and blue growth chart"></div>
</section>

<section class="abs welcome">
  <h1>Welcome to <strong>Amberbolt</strong> Digital Marketing..</h1>
  <p class="lead">Phasellus felis dolor scelerisque a tempus eget lobortis id l</p>
  <p class="body">Praesent sit amet est. In dictum, dolor eu dictum porttitor, enim felis viverra mi, eget luctus massa purus quis odio. Etiam nulla massa, pharetra facili-sis, volutpat in, imperdiet sit amet, sem. Aliquam nec erat at purus cursus interdum. Vestibulum ligula augue, bibendum accumsan, vestibulum</p>
</section>

<section class="abs products">
  <h2>Our Products</h2>
  <div class="product" style="left:46px">
    <div class="thumb" role="img" aria-label="Business person holding a tablet with a glowing globe" style="background:linear-gradient(135deg,#2d4f6e,#6f9fc4 60%,#8aa0b0)"></div>
    <h3>Product Tittle</h3>
    <p>Vivamus porttitor purus nisi eleifend libero tempus libero lectus feugiat felis Morbi diam mauris viverra.</p>
  </div>
  <div class="product" style="left:216px">
    <div class="thumb" role="img" aria-label="Hands reviewing charts on a tablet" style="background:linear-gradient(135deg,#7a8fa3,#cfe0ee 55%,#9fb6c9)"></div>
    <h3>Product Tittle</h3>
    <p>Vivamus porttitor purus nisi eleifend libero tempus libero lectus feugiat felis Morbi diam mauris viverra.</p>
  </div>
  <div class="product" style="left:388px">
    <div class="thumb" role="img" aria-label="Tablet projecting a team of figures" style="background:linear-gradient(135deg,#0f2a3c,#2d7fa6 55%,#12384e)"></div>
    <h3>Product Tittle</h3>
    <p>Vivamus porttitor purus nisi eleifend libero tempus libero lectus feugiat felis Morbi diam mauris viverra.</p>
  </div>
  <div class="product" style="left:559px">
    <div class="thumb" role="img" aria-label="Hands holding a tablet with a blue bar chart" style="background:linear-gradient(135deg,#d8e4ee,#f4f7fa 50%,#b5cde0)"></div>
    <h3>Product Tittle</h3>
    <p>Vivamus porttitor purus nisi eleifend libero tempus libero lectus feugiat felis Morbi diam mauris viverra.</p>
  </div>
</section>

<h2 class="abs section-title services-title"><strong>Services</strong> We Provide</h2>

<div class="service" style="left:45px;top:858px"><div class="icon" role="img" aria-label="Target icon" style="background:#d9332b"></div><div><h4>Services Tittle</h4><p>Duis tincidunt lectus quis dui viverra vestibulum Suspendisse</p></div></div>
<div class="service" style="left:260px;top:858px"><div class="icon" role="img" aria-label="Rocket icon" style="background:#41566f"></div><div><h4>Services Tittle</h4><p>Duis tincidunt lectus quis dui viverra vestibulum Suspendisse</p></div></div>
<div class="service" style="left:45px;top:925px"><div class="icon" role="img" aria-label="Map pin icon" style="background:#8cc269"></div><div><h4>Services Tittle</h4><p>Duis tincidunt lectus quis dui viverra vestibulum Suspendisse</p></div></div>
<div class="service" style="left:260px;top:925px"><div class="icon" role="img" aria-label="Star icon" style="background:#7fb5dc"></div><div><h4>Services Tittle</h4><p>Duis tincidunt lectus quis dui viverra vestibulum Suspendisse</p></div></div>
<div class="service" style="left:45px;top:996px"><div class="icon" role="img" aria-label="Pencil icon" style="background:#a7cf7c"></div><div><h4>Services Tittle</h4><p>Duis tincidunt lectus quis dui viverra vestibulum Suspendisse</p></div></div>
<div class="service" style="left:260px;top:996px"><div class="icon" role="img" aria-label="Line chart icon" style="background:#82b4dd"></div><div><h4>Services Tittle</h4><p>Duis tincidunt lectus quis dui viverra vestibulum Suspendisse</p></div></div>

<h2 class="abs section-title blog-title"><strong>Recent</strong> Blog Feed</h2>
<aside class="abs blog-box">
  <div class="blog-item" style="padding-top:12px"><h5>Blog Post Tittle</h5><p>Morbi porta, libero id ullamcorper nonummy nibh ligula pulvinar metus eget</p></div>
  <div class="blog-item"><h5>Blog Post Tittle</h5><p>Lorem ipsum dolor sit amet consectetuer</p></div>
  <div class="blog-item"><h5>Blog Post Tittle</h5><p>Morbi porta, libero id ullamcorper nonummy, nibh ligula pulvinar metus eget</p></div>
  <div class="blog-item"><h5>Blog Post Tittle</h5><p>Suspendisse vulputate aliquam du</p></div>
  <div class="blog-more">View More feed
    <svg width="6" height="7" viewBox="0 0 6 7" style="vertical-align:-1px"><path d="M1 0.5L5 3.5L1 6.5Z" fill="#333"/></svg>
  </div>
</aside>

<footer class="abs site-footer">
  <div class="abs footer-nav">HOME <span>|</span> ABOUT US <span>|</span> PRODUCTS <span>|</span> SUCCESS STORIES <span>|</span> BLOG <span>|</span> CONTACT US</div>
  <div class="abs copyright">Copyright © 2013 Company Name. All right reserved</div>
  <div class="abs badge-a" role="img" aria-label="Partner badge"></div>
  <div class="abs badge-b" role="img" aria-label="Accreditation badge"></div>
</footer>

</body>
</html>
```